Biz Card

MARKETING today is the most rapidly changing business discipline. Media options to reach customers, actual customer preferences and consumer buying decisions change by the minute . . . no, by the second. The behavioral data generated by all aspects of the business and the new technologies that put the data to work together produce the potential to generate business intelligence and guide smart resource allocation to influence purchase and retention. However, to realize this potential, marketing professionals at all levels and in all organizations must continuously improve their skills not just from on-the-job training but by learning from masters in the field. The Bright Horizon Guild is the training center that serves this professional development need.model logos:msi.orgama.orgcontentmarketinginstitute.comBook covers on MarketingMetrics, Marketing Anaytics
Industry/Entity Type
Business
Contact Information for Business Card
Roy A. YoungCEOMarketing Science Academyphone: 310-601-4755email: roy@marketingscience.comAddress:437 South Rexford DriveBeverly Hills, CA 89377
Look and feel
Each slider illustrates characteristics of the customer's brand and the style your logo design should communicate.

```html
<!DOCTYPE html>
<html lang="en">
<head>
<meta charset="utf-8">
<title>Bright Horizon Guild — Business Card</title>
<link rel="stylesheet" href="https://fonts.googleapis.com/css2?family=Roboto:wght@400;500;700&display=swap">
<style>
  :root {
    --backdrop: #a8a6a6;
    --brand-red: #8b2924;
    --paper: #f6f6f5;
    --ink: #4a4a4a;
    --ink-soft: #5a5a5a;
    --rule: #6a6a6a;
    --white: #ffffff;
  }
  * { box-sizing: border-box; margin: 0; padding: 0; }
  html, body { width: 1200px; height: 1200px; overflow: hidden; }
  body {
    position: relative;
    background: var(--backdrop);
    font-family: "Roboto", Arial, sans-serif;
  }
  .card { position: absolute; width: 713px; height: 418px; }
  .card-front { left: 238px; top: 118px; background: var(--brand-red); }
  .card-back { left: 230px; top: 644px; background: var(--paper); }

  .wordmark {
    display: flex; align-items: center; gap: 18px;
    font-weight: 700; text-transform: uppercase;
    line-height: 1.02; letter-spacing: 0.5px;
  }
  .wordmark-dot { width: 22px; height: 22px; border-radius: 50%; flex: none; }
  .wordmark-name { font-size: 34px; }

  .card-front .wordmark {
    position: absolute; left: 0; right: 0; top: 158px;
    justify-content: center; color: var(--white);
  }
  .card-front .wordmark-dot { background: var(--white); }

  .card-back .wordmark {
    position: absolute; left: 43px; top: 44px; color: var(--brand-red);
  }
  .card-back .wordmark-dot { background: var(--brand-red); }

  .holder-name {
    position: absolute; left: 42px; top: 208px;
    font-size: 25px; font-weight: 700; color: var(--brand-red);
  }
  .holder-title {
    position: absolute; left: 44px; top: 246px;
    font-size: 14px; font-weight: 400; color: var(--ink-soft);
  }
  .title-rule {
    position: absolute; left: 86px; top: 260px; width: 585px;
    border-top: 1.5px solid var(--rule);
  }
  .contact-list {
    position: absolute; left: 44px; top: 306px; list-style: none;
    font-size: 17px; color: var(--ink); line-height: 24px;
  }
  .contact-list li { display: flex; align-items: center; gap: 18px; }
  .contact-list svg { width: 16px; height: 16px; fill: var(--brand-red); flex: none; }
  .address {
    position: absolute; right: 41px; top: 306px; text-align: left;
    font-size: 17px; color: var(--ink); line-height: 24px; font-style: normal;
  }
</style>
</head>
<body>
  <section class="card card-front">
    <div class="wordmark">
      <span class="wordmark-dot"></span>
      <span class="wordmark-name">Bright<br>Horizon<br>Guild</span>
    </div>
  </section>

  <section class="card card-back">
    <div class="wordmark">
      <span class="wordmark-dot"></span>
      <span class="wordmark-name">Bright<br>Horizon<br>Guild</span>
    </div>

    <h1 class="holder-name">Neil P. Barton</h1>
    <p class="holder-title">CEO</p>
    <div class="title-rule"></div>

    <ul class="contact-list">
      <li>
        <svg viewBox="0 0 16 16" aria-hidden="true"><path d="M2 5c0-2 3-3 6-3s6 1 6 3v1h-3V5H5v1H2z M4 7h8l2 6H2z M8 8.5a2 2 0 1 0 0 4a2 2 0 0 0 0-4z"/></svg>
        555-555-0182
      </li>
      <li>
        <svg viewBox="0 0 16 16" aria-hidden="true"><path d="M1 3h14v10H1z M2 4.2v.4l6 4.2 6-4.2v-.4z" fill-rule="evenodd"/></svg>
        neil@brighthorizonguild.com
      </li>
      <li>
        <svg viewBox="0 0 16 16" aria-hidden="true"><path d="M8 1a7 7 0 1 0 0 14A7 7 0 0 0 8 1zm0 1.5c.8 0 1.6 1.6 1.9 4H6.1C6.4 4.1 7.2 2.5 8 2.5zM2.6 6.5a5.6 5.6 0 0 1 2.6-3.3 9 9 0 0 0-.6 3.3zm0 3h2a9 9 0 0 0 .6 3.3 5.6 5.6 0 0 1-2.6-3.3zM8 13.5c-.8 0-1.6-1.6-1.9-4h3.8c-.3 2.4-1.1 4-1.9 4zm-2-5.3V8v-.2h4v.4zm4.8 4.6a9 9 0 0 0 .6-3.3h2a5.6 5.6 0 0 1-2.6 3.3zm.6-6.3a9 9 0 0 0-.6-3.3 5.6 5.6 0 0 1 2.6 3.3z"/></svg>
        www.brighthorizonguild.com
      </li>
    </ul>

    <address class="address">
      912 North Calloway Lane<br>
      Larkspur Vale, NV 89377
    </address>
  </section>
</body>
</html>
```